Corvane Business Cards

Front of business card will have logo, name, address, & telephone number. Back of card will have a list of services provided - Roads, Substation Pads, Temporary Pads, Site Pads, Land Leveling, Powerline Row Cleaning, Land Clearing, Gates, Fencing, Construction Entrances, Excavation, Trenching, Underground Utilities, Directional Boring, Pile Driving. We are a construction company that uses heavy equipment like bulldozers, motor graders/blades, dump trucks, backhoes, hydro axes, & skid loaders. We build roads, pads, & install electric utility lines & waterlines underground. This logo is new. The word "Construction" can be smaller as uploaded 2 example edited logos. We will be using this card design for many employees.
Target Market(s)
Industrial Electric Powerline, Wind Turbine, Solar Panel, & Water Utility companies.
Contact Information for Business Card
Name/Position - Dwayne Halster - Owner
Address: 4875 FM 309
Calloway, NM 88412
Phone number - (325) 482-5096

```html
<!DOCTYPE html>
<html lang="en">
<head>
<meta charset="utf-8">
<title>Corvane Construction Business Cards</title>
<link href="https://fonts.googleapis.com/css2?family=Roboto:ital,wght@0,400;0,700;1,400&family=Marcellus&display=swap" rel="stylesheet">
<style>
  :root {
    --backdrop: #1b1b1d;
    --card: #3a111b;
    --ink: #ffffff;
    --ink-soft: rgba(255,255,255,0.85);
  }
  * { margin: 0; padding: 0; box-sizing: border-box; }
  html, body {
    width: 1200px; height: 900px; overflow: hidden;
    background: var(--backdrop);
  }
  .sheet {
    width: 1200px; height: 900px;
    display: flex; flex-direction: column; align-items: center; justify-content: center;
    gap: 40px;
  }
  .card {
    width: 700px; height: 400px;
    background: var(--card);
    color: var(--ink);
    position: relative;
    box-shadow: 0 14px 30px rgba(0,0,0,0.55);
    font-family: "Roboto", Arial, sans-serif;
    overflow: hidden;
  }
  /* Front */
  .card--front { display: flex; align-items: center; padding: 0 40px; }
  .brand { display: flex; flex-direction: column; align-items: flex-end; width: 240px; flex: none; }
  .brand__mark { display: flex; align-items: center; gap: 10px; }
  .brand__square { width: 18px; height: 18px; background: var(--ink); flex: none; }
  .brand__name { font-weight: 700; font-size: 32px; letter-spacing: 3px; white-space: nowrap; }
  .brand__sub {
    font-family: "Marcellus", Georgia, serif;
    font-size: 28px; letter-spacing: 1px; margin-top: 6px; white-space: nowrap;
  }
  .divider { width: 1px; height: 150px; background: var(--ink); margin: 0 30px; flex: none; }
  .contact { display: flex; flex-direction: column; white-space: nowrap; }
  .contact__name { font-weight: 700; font-size: 22px; letter-spacing: 1px; text-transform: uppercase; }
  .contact__role { font-style: italic; font-size: 17px; color: var(--ink-soft); margin-bottom: 18px; }
  .contact__line { display: flex; align-items: center; gap: 10px; font-size: 17px; margin-top: 8px; }
  .contact__icon { width: 16px; height: 16px; flex: none; }
  /* Back */
  .card--back { display: flex; flex-direction: column; align-items: flex-end; padding: 70px 40px 0 40px; }
  .back-brand { display: flex; align-items: center; gap: 14px; align-self: center; margin-bottom: 54px; }
  .back-brand .brand__square { width: 30px; height: 30px; }
  .back-brand .brand__name { font-size: 64px; letter-spacing: 6px; }
  .services { text-align: right; font-size: 15px; line-height: 1.9; letter-spacing: 0.3px; white-space: nowrap; }
</style>
</head>
<body>
<main class="sheet">
  <section class="card card--front" aria-label="Business card front">
    <div class="brand">
      <div class="brand__mark">
        <span class="brand__square"></span>
        <span class="brand__name">CORVANE</span>
      </div>
      <div class="brand__sub">CONSTRUCTION</div>
    </div>
    <div class="divider"></div>
    <div class="contact">
      <div class="contact__name">Dwayne Halster</div>
      <div class="contact__role">Owner</div>
      <div class="contact__line">
        <svg class="contact__icon" viewBox="0 0 24 24" aria-hidden="true"><path fill="#fff" d="M6.6 10.8a15.1 15.1 0 0 0 6.6 6.6l2.2-2.2c.3-.3.7-.4 1-.2 1.1.4 2.3.6 3.6.6.6 0 1 .4 1 1V20c0 .6-.4 1-1 1C10.6 21 3 13.4 3 4c0-.6.4-1 1-1h3.5c.6 0 1 .4 1 1 0 1.3.2 2.5.6 3.6.1.3 0 .7-.2 1z"/></svg>
        <span>(325) 482-5096</span>
      </div>
      <div class="contact__line">
        <svg class="contact__icon" viewBox="0 0 24 24" aria-hidden="true"><path fill="#fff" d="M12 2a7 7 0 0 0-7 7c0 5.2 7 13 7 13s7-7.8 7-13a7 7 0 0 0-7-7zm0 9.5A2.5 2.5 0 1 1 12 6.5a2.5 2.5 0 0 1 0 5z"/></svg>
        <span>4875 FM 309 Calloway, NM 88412</span>
      </div>
    </div>
  </section>

  <section class="card card--back" aria-label="Business card back">
    <div class="back-brand">
      <span class="brand__square"></span>
      <span class="brand__name">CORVANE</span>
    </div>
    <p class="services">
      Roads / Substation Pads / Temporary Pads / Site Pads / Land Leveling<br>
      Land Clearing / Gates / Fencing / Construction Entrances / Excavation / Trenching<br>
      Underground Utilities / Powerline Row Cleaning / Pile Driving / Directional Boring
    </p>
  </section>
</main>
</body>
</html>
```